Moravel Aesthetic Doctor

I require an elegant, luxurious looking business card for my aesthetic business. I am a doctor and that will set me aside from competitors. I am planning to provide home and spa based treatments to clients with high expectations. I have attached my logo.

```html
<!DOCTYPE html>
<html lang="en">
<head>
<meta charset="utf-8">
<title>Moravel Aesthetic Doctor — Business Card</title>
<link href="https://fonts.googleapis.com/css2?family=Roboto:wght@300;400;500;700&display=swap" rel="stylesheet">
<style>
  :root{
    --backdrop:#3a3a3c;
    --card:#1c1c1e;
    --sky:#4fb3e8;
    --silver:#c4cad3;
    --white:#f4f6f8;
    --grey:#d5d8dc;
  }
  *{margin:0;padding:0;box-sizing:border-box}
  html,body{width:799px;height:1200px;overflow:hidden}
  body{background:var(--backdrop);font-family:'Roboto',Arial,sans-serif;position:relative}
  .card{position:absolute;left:70px;width:660px;height:377px;background:var(--card);
    box-shadow:0 18px 40px rgba(0,0,0,.45);overflow:hidden}
  .card--front{top:160px}
  .card--back{top:680px}

  .brand{position:absolute;display:flex;align-items:center;gap:16px}
  .brand__dot{width:58px;height:58px;border-radius:50%;border:2px solid var(--silver);flex:none}
  .brand__name{font-weight:300;color:var(--silver);line-height:1.05;letter-spacing:3px;text-transform:uppercase}
  .brand__name span{display:block}
  .card--front .brand{left:120px;top:52px}
  .card--front .brand__name{font-size:38px}
  .card--front .brand__name span:last-child{font-size:22px;letter-spacing:5px}
  .card--back .brand{left:40px;top:150px}
  .card--back .brand__name{font-size:30px}
  .card--back .brand__name span:last-child{font-size:17px;letter-spacing:4px}

  .services{position:absolute;left:0;right:0;top:196px;text-align:center;color:var(--white);
    font-size:18px;line-height:1.45;border-top:6px solid var(--sky);padding-top:14px}
  .services .sep{margin:0 10px}
  .tagline{position:absolute;left:0;right:0;top:288px;height:40px;background:var(--sky);
    color:var(--white);font-size:19px;letter-spacing:1.5px;text-transform:uppercase;
    display:flex;align-items:center;justify-content:center}

  .contact{position:absolute;left:388px;top:120px;width:250px;color:var(--grey)}
  .contact__name{font-size:21px;font-weight:700;color:var(--silver)}
  .contact__name small{font-size:11px;font-weight:400;color:var(--sky);margin-left:4px}
  .contact__cred{font-size:15px;color:var(--sky);line-height:1.25;margin:4px 0 14px}
  .contact__row{display:flex;align-items:center;gap:10px;font-size:15px;margin-bottom:5px}
  .contact__row svg{width:13px;height:13px;fill:var(--grey);flex:none}
  .contact__social{font-size:15px;margin-top:6px}
  .contact__social b{font-weight:500;color:var(--sky)}
</style>
</head>
<body>
  <section class="card card--front">
    <div class="brand">
      <div class="brand__dot"></div>
      <div class="brand__name"><span>Moravel</span><span>Aesthetic Doctor</span></div>
    </div>
    <div class="services">
      Dermal Injectables<span class="sep">|</span>Plasma Facials<span class="sep">|</span>Microneedling<br>
      Skin Boosters<span class="sep">|</span>Excessive Sweating
    </div>
    <div class="tagline">Home and Spa Based Treatments</div>
  </section>

  <section class="card card--back">
    <div class="brand">
      <div class="brand__dot"></div>
      <div class="brand__name"><span>Moravel</span><span>Aesthetic Doctor</span></div>
    </div>
    <div class="contact">
      <p class="contact__name">Dr Elsa Venner<small>MRCPCH MD</small></p>
      <p class="contact__cred">Australasian Diploma<br>of Aesthetic Medicine</p>
      <p class="contact__row"><svg viewBox="0 0 24 24"><path d="M6.6 10.8a15 15 0 0 0 6.6 6.6l2.2-2.2c.3-.3.7-.4 1-.2 1.1.4 2.3.6 3.6.6.6 0 1 .4 1 1V20c0 .6-.4 1-1 1A17 17 0 0 1 3 4c0-.6.4-1 1-1h3.5c.6 0 1 .4 1 1 0 1.3.2 2.5.6 3.6.1.3 0 .7-.2 1z"/></svg>0800 345 918</p>
      <p class="contact__row"><svg viewBox="0 0 24 24"><path d="M2 5h20v14H2zm2 2v.5l8 5 8-5V7z"/></svg>elsa@moravel.co.nz</p>
      <p class="contact__row"><svg viewBox="0 0 24 24"><circle cx="12" cy="12" r="9" fill="none" stroke="#d5d8dc" stroke-width="2"/><path d="M3 12h18M12 3c3 3 3 15 0 18M12 3c-3 3-3 15 0 18" fill="none" stroke="#d5d8dc" stroke-width="1.6"/></svg>www.moravel.co.nz</p>
      <p class="contact__social">Follow us on: <b>@moravelaesthetic</b></p>
    </div>
  </section>
</body>
</html>
```